Brightway Haus Inc. Business Card Design

Brightway Haus Inc. is in search of a great clean design for our business cards!

Looking to incorporate our full logo and watermark on side one (however, I am open to having the text and watermark separated within the design.)

On side two, I am looking to have contact information (Name, Position, Phone #, Email, Website (www.thebrightwayhaus.ca). Can have the logo and/or watermark as part of the design if applicable.

Please add tagline "Where Shine Counts" on either side 1 or 2. This tagline can be in a sans serif, serif or cursive font as long as it compliments overall design. Capitalization can be title or sentence case depending on how it fits within the design.

Get creative!! Looking for a clean, crisp, premium design! Looking for a glossy card finish with spot UV features when printed. Cards will also be printed with rounded corners. Standard dimensions (3.5 x 2).

Target Market(s)

B2B - primary clients are business owners or property management corporations. (residential jobs are few and far between)

Industry/Entity Type

Business

Contact Information for Business Card

- clean, crisp design
- double sided
- spot UV accents and glossy finish upon printing
- standard business card size (3.5 x 2) with rounded corners
- please see project description for requirements per side

Font styles to use
Sans Serif

Requirements
Must have
• - adequate bleeds with print ready files
• - cohesive design elements between side 1 & 2
• - spot UV elements (can be on both sides or just one, use your discretion)
• - colour pallet should match the logo file provided
• - incorporate tagline "where shine counts" (this tagline can be in a serif or sans serif font as long as it is complimentary to the overall design.
Nice to have
• - Premium elements with a clean design
Should not have
• - Please omit cartoon or whimsical like designs, think premium.
• - Colours should not stray from the pallet of the provided logo.

```html
<!DOCTYPE html>
<html lang="en">
<head>
<meta charset="utf-8">
<title>Brightway Haus Inc. Business Cards</title>
<link href="https://fonts.googleapis.com/css2?family=Open+Sans:wght@700&family=Roboto:wght@400;500;700&display=swap" rel="stylesheet">
<style>
  :root {
    --backdrop: #2a2a2b;
    --card-white: #f4f4f3;
    --teal: #12b9bb;
    --navy: #1c2452;
    --grey: #9a9a9c;
    --text-grey: #5c5c5e;
    --white: #ffffff;
  }
  * { margin: 0; padding: 0; box-sizing: border-box; }
  html, body {
    width: 1200px; height: 960px; overflow: hidden;
    background: var(--backdrop);
    font-family: "Roboto", Arial, sans-serif;
  }
  .card {
    position: absolute; left: 320px;
    width: 600px; height: 342px;
    border-radius: 16px; overflow: hidden;
    background: var(--card-white);
  }
  .card--front { top: 100px; }
  .card--back { top: 493px; }

  .brand-watermark {
    position: absolute; left: 0; top: 15px;
    width: 335px; height: 327px;
    border-radius: 0 10px 0 0;
    background: linear-gradient(160deg, var(--teal) 0%, #1a8b9d 45%, var(--navy) 100%);
    opacity: 0.9;
  }
  .front-wordmark {
    position: absolute; right: 36px; top: 263px;
    text-align: left;
  }
  .brand-name {
    font-family: "Open Sans", Arial, sans-serif;
    font-weight: 700; color: var(--teal);
    letter-spacing: -0.3px; white-space: nowrap;
  }
  .front-wordmark .brand-name { font-size: 19px; }
  .tagline {
    margin-top: 5px;
    font-size: 14.5px; color: var(--text-grey);
    letter-spacing: 1.6px; white-space: nowrap;
  }

  .back-swoosh { position: absolute; inset: 0; }
  .back-logo {
    position: absolute; left: 32px; top: 62px;
    display: flex; align-items: center; gap: 10px;
  }
  .back-logo__square {
    width: 34px; height: 34px; background: var(--teal);
  }
  .back-logo .brand-name { font-size: 29px; }

  .holder {
    position: absolute; left: 32px; top: 270px;
  }
  .holder__name {
    font-size: 20px; font-weight: 500; color: var(--teal);
    letter-spacing: 0.2px;
  }
  .holder__role {
    font-size: 14.5px; font-weight: 700; color: var(--white);
  }

  .contact-list {
    position: absolute; right: 44px; top: 178px;
    list-style: none; text-align: right;
    color: var(--white); font-size: 14.5px; line-height: 19.3px;
  }
  .contact-list li { display: flex; justify-content: flex-end; align-items: center; gap: 8px; }
  .contact-icon { width: 12px; height: 12px; flex: none; }
  .contact-list .no-icon { padding-right: 20px; }
</style>
</head>
<body>
  <section class="card card--front" aria-label="Card front">
    <div class="brand-watermark" role="img" aria-label="Large brand watermark area"></div>
    <div class="front-wordmark">
      <div class="brand-name">BRIGHTWAY HAUS INC.</div>
      <div class="tagline">Where Shine Counts</div>
    </div>
  </section>

  <section class="card card--back" aria-label="Card back">
    <svg class="back-swoosh" width="600" height="342" viewBox="0 0 600 342" aria-hidden="true">
      <path d="M0,176 C70,226 200,226 330,160 S540,12 600,-6 L600,342 L0,342 Z" fill="var(--teal)"/>
      <path d="M0,188 C70,236 200,236 330,172 S540,22 600,4 L600,342 L0,342 Z" fill="var(--navy)"/>
      <path d="M0,188 C70,236 200,236 330,172 S540,22 600,4" fill="none" stroke="var(--white)" stroke-width="3"/>
    </svg>

    <div class="back-logo">
      <span class="back-logo__square"></span>
      <span class="brand-name">BRIGHTWAY HAUS INC.</span>
    </div>

    <div class="holder">
      <div class="holder__name">DANIEL REYES</div>
      <div class="holder__role">CEO/FOUNDER</div>
    </div>

    <ul class="contact-list">
      <li>555 210 4817
        <svg class="contact-icon" viewBox="0 0 12 12" aria-label="Phone"><path d="M2.5 0.8 L4.4 0.8 L5 3.6 L3.8 4.6 Q5 7.2 7.4 8.2 L8.4 7 L11.2 7.6 L11.2 9.5 Q11 11.3 9.2 11.2 Q1.2 10.4 0.8 2.8 Q0.8 0.9 2.5 0.8 Z" fill="var(--teal)"/></svg>
      </li>
      <li>555 384 1926
        <svg class="contact-icon" viewBox="0 0 12 12" aria-label="Mobile"><rect x="3" y="0.5" width="6" height="11" rx="1.2" fill="none" stroke="var(--teal)" stroke-width="1.2"/><rect x="5" y="9.3" width="2" height="1" fill="var(--teal)"/></svg>
      </li>
      <li>555 672 3059
        <svg class="contact-icon" viewBox="0 0 12 12" aria-label="Fax"><rect x="3" y="1" width="6" height="3" fill="var(--teal)"/><rect x="0.5" y="4.5" width="11" height="5" rx="1" fill="var(--teal)"/><rect x="3" y="8" width="6" height="3.5" fill="var(--teal)" stroke="var(--navy)" stroke-width="0.8"/></svg>
      </li>
      <li>hello@thebrightwayhaus.ca
        <svg class="contact-icon" viewBox="0 0 12 12" aria-label="Email"><rect x="0.5" y="2.5" width="11" height="7.5" fill="var(--teal)"/><path d="M0.8 2.8 L6 7 L11.2 2.8" fill="none" stroke="var(--navy)" stroke-width="1"/></svg>
      </li>
      <li>www.thebrightwayhaus.ca
        <svg class="contact-icon" viewBox="0 0 12 12" aria-label="Website"><circle cx="6" cy="6" r="5.2" fill="none" stroke="var(--teal)" stroke-width="1.2"/><ellipse cx="6" cy="6" rx="2.2" ry="5.2" fill="none" stroke="var(--teal)" stroke-width="1"/><path d="M0.8 6 H11.2" stroke="var(--teal)" stroke-width="1"/></svg>
      </li>
      <li class="no-icon">214 Harbour Street</li>
      <li class="no-icon">Halifax, Nova Scotia 30418</li>
    </ul>
  </section>
</body>
</html>
```